Computer Service Provider in Need of New Letterhead Design

We are BrackenLoop Computer Services, a computer/IT services company that provides IT Support, software, hardware, virus monitoring, etc. in Vermont. We are looking for new letterhead, that is both professional and matches the current theme of our business cards & website.
Please note that we want to include the following information:
www.BrackenLoop.example
802-471-3926
742 Hollis Meadow Lane, Fernbrook, VT 05999
Proactive Solutions • Approachable People • Proven Performance
I will be attaching our logo along with the business card images.
We would love to have the

```html
<!DOCTYPE html>
<html lang="en">
<head>
<meta charset="utf-8">
<title>BrackenLoop Computer Services – Letterhead</title>
<link rel="stylesheet" href="https://fonts.googleapis.com/css2?family=Arimo:wght@400;700&display=swap">
<style>
  :root {
    --brand-blue: #25557c;
    --brand-orange: #e3861f;
    --paper: #ffffff;
    --backdrop: #eeeeee;
    --ink-light: #ffffff;
  }
  html, body {
    margin: 0;
    padding: 0;
    width: 1200px;
    height: 795px;
    overflow: hidden;
    background: var(--backdrop);
    font-family: "Arimo", Arial, sans-serif;
  }
  .letterhead {
    position: absolute;
    left: 315px;
    top: 30px;
    width: 569px;
    height: 735px;
    background: var(--paper);
    box-shadow: 0 2px 10px rgba(0,0,0,0.12);
    overflow: hidden;
  }
  .brand {
    position: absolute;
    left: 42px;
    top: 40px;
    display: flex;
    align-items: center;
    gap: 8px;
  }
  .brand-square {
    width: 30px;
    height: 30px;
    background: var(--brand-blue);
  }
  .brand-name {
    color: var(--brand-blue);
    font-weight: 700;
    font-size: 15px;
    line-height: 1.05;
    margin: 0;
  }
  .footer-art {
    position: absolute;
    left: 0;
    bottom: 0;
  }
  .tagline {
    position: absolute;
    left: 14px;
    bottom: 5px;
    margin: 0;
    color: var(--ink-light);
    font-size: 11px;
    letter-spacing: 0.2px;
    white-space: nowrap;
  }
  .contact {
    position: absolute;
    right: 18px;
    bottom: 22px;
    margin: 0;
    font-style: normal;
    color: var(--ink-light);
    font-size: 9px;
    line-height: 1.45;
    text-align: right;
  }
  .contact-divider {
    display: block;
    width: 150px;
    height: 1px;
    margin: 4px 0 4px auto;
    background: var(--brand-orange);
  }
  .contact-line {
    display: flex;
    justify-content: flex-end;
    align-items: center;
    gap: 4px;
  }
  .contact-icon {
    width: 8px;
    height: 8px;
  }
</style>
</head>
<body>
  <main class="letterhead">
    <header class="brand">
      <span class="brand-square" aria-hidden="true"></span>
      <p class="brand-name">BrackenLoop<br>Computer Services</p>
    </header>

    <svg class="footer-art" width="569" height="110" viewBox="0 0 569 110" aria-hidden="true">
      <rect x="0" y="86" width="390" height="24" fill="var(--brand-orange)"/>
      <polygon points="395,0 569,0 569,110 382,110 352,70" fill="var(--brand-blue)"/>
    </svg>

    <p class="tagline">Steady Support | Friendly Experts | Reliable Results</p>

    <address class="contact">
      742 Hollis Meadow Lane<br>
      Fernbrook, VT 05999
      <span class="contact-divider"></span>
      <span class="contact-line">
        <svg class="contact-icon" viewBox="0 0 10 10" aria-hidden="true">
          <path d="M2 1h2l1 2.5-1.3 1a6 6 0 0 0 2.8 2.8l1-1.3L10 7v2a1 1 0 0 1-1 1A9 9 0 0 1 0 2a1 1 0 0 1 1-1z" fill="var(--ink-light)"/>
        </svg>
        802-471-3926
      </span>
      <span class="contact-line">
        <svg class="contact-icon" viewBox="0 0 10 10" aria-hidden="true">
          <circle cx="5" cy="5" r="4.3" fill="none" stroke="var(--ink-light)" stroke-width="1"/>
          <ellipse cx="5" cy="5" rx="1.9" ry="4.3" fill="none" stroke="var(--ink-light)" stroke-width="0.8"/>
          <line x1="0.7" y1="5" x2="9.3" y2="5" stroke="var(--ink-light)" stroke-width="0.8"/>
        </svg>
        www.BrackenLoop.example
      </span>
    </address>
  </main>
</body>
</html>
```